Create a web design for a vehicle codes lookup website

Create a bright and fun web design to replace our current boring one!

-Make a new design for this page that shows vehicle codes information: http://plexora.site/vin/dara-pellow.4182.html
-Click "Random VIN" to see more examples.
-The page shows the vehicle information (see above example) is the most important one to add a redesign to. Bonus points if you create a redesign for the main page as well: plexora.site.

Number of Pages Required

2 page

Requirements
Must have
• Be fun and have bright colors!
Should not have
• Do not add pictures of specific people or vehicles unless they can be used on every page. The example page has a Morvane Tessly, but do not add a picture of the Morvane Tessly because other pages have different vehicles.

```html
<!DOCTYPE html>
<html lang="en">
<head>
<meta charset="utf-8">
<title>4P7KD29R813560742 Vehicle Purchase Information</title>
<link href="https://fonts.googleapis.com/css2?family=Open+Sans:wght@400;600;700&display=swap" rel="stylesheet">
<style>
:root{
  --page-bg:#eef0f2;
  --header-bg:#f7f8f9;
  --nav-bg:#1c3f73;
  --nav-active:#2b6fc0;
  --brand-blue:#2a78d0;
  --hero-blue:#2f8ee6;
  --hero-light:#5aaef0;
  --heading:#2a3440;
  --text:#6b7580;
  --label:#2a78d0;
  --line:#dde2e7;
  --white:#ffffff;
  --footer-bg:#3a3e44;
  --footer-bottom:#2d3035;
  --social:#e0463a;
}
*{box-sizing:border-box;margin:0;padding:0}
html,body{width:1200px;height:2236px;overflow:hidden}
body{background:var(--page-bg);font-family:"Open Sans",Arial,sans-serif;color:var(--text);position:relative}
.site-header{height:148px;background:var(--header-bg);position:relative;border-bottom:1px solid var(--line)}
.brand{position:absolute;left:52px;top:30px;display:flex;align-items:center;gap:14px}
.brand-mark{width:64px;height:64px;background:var(--brand-blue);border-radius:6px}
.brand-name{color:var(--brand-blue);font-weight:700;font-size:25px;line-height:28px;text-transform:uppercase}
.search{position:absolute;right:70px;top:36px;width:200px;height:28px;border:1px solid #c9cfd6;background:#fff;font-size:12px;color:#9aa3ac;padding:5px 10px}
.social{position:absolute;right:70px;top:78px;display:flex;gap:6px}
.social span{width:22px;height:22px;background:var(--social);border-radius:3px;display:block}
.main-nav{height:40px;background:var(--nav-bg);display:flex;padding-left:40px}
.main-nav a{color:#fff;font-size:12px;font-weight:600;text-decoration:none;text-transform:uppercase;padding:0 28px;line-height:40px}
.main-nav a.active{background:var(--nav-active)}
.content{position:absolute;left:40px;top:188px;width:1120px;height:1957px;background:var(--white);padding:32px 40px}
.hero{height:220px;background:linear-gradient(180deg,var(--hero-light),var(--hero-blue));display:flex;align-items:center;justify-content:center;text-align:center}
.hero h1{color:#fff;font-size:56px;line-height:68px;font-weight:600;width:820px}
.section-title{font-size:22px;font-weight:600;color:var(--heading);display:flex;align-items:center;gap:10px}
.section-title::before{content:"";width:18px;height:18px;border-radius:50%;background:var(--brand-blue)}
.section-title strong{color:var(--heading);font-weight:700}
.title-customer{margin-top:52px}
.detail-grid{margin-top:20px;display:grid;grid-template-columns:repeat(4,1fr);border:1px solid var(--line);height:255px}
.detail-col{border-right:1px solid var(--line)}
.detail-col:last-child{border-right:none}
.detail-col h3{background:var(--brand-blue);color:#fff;font-size:15px;font-weight:600;height:44px;line-height:44px;padding-left:44px;position:relative}
.detail-col h3::before{content:"";position:absolute;left:16px;top:14px;width:16px;height:16px;border:2px solid #fff;border-radius:3px}
.detail-col ul{list-style:none;padding:18px 20px}
.detail-col li{font-size:13px;line-height:30px;color:var(--text)}
.detail-col li b{color:var(--heading);font-weight:600}
.title-fuel{margin-top:140px}
.fuel-table{margin-top:20px;display:grid;grid-template-columns:1fr 1fr;column-gap:40px;height:400px;border-top:1px solid var(--line)}
.fuel-cell{border-bottom:1px solid var(--line);padding:10px 10px;height:57px}
.fuel-cell h4{font-size:14px;color:var(--label);font-weight:600;line-height:19px}
.fuel-cell p{font-size:12px;line-height:17px}
.title-court{margin-top:44px}
.action-bar{margin-top:22px;height:40px;background:var(--brand-blue);color:#fff;font-size:15px;font-weight:600;line-height:40px;padding-left:20px;display:flex;align-items:center;gap:10px}
.action-bar::before{content:"";width:14px;height:14px;background:#fff;border-radius:2px}
.body-text{margin-top:30px;font-size:13px;line-height:22px}
.body-text + .body-text{margin-top:22px}
.title-vin{margin-top:44px}
.site-footer{position:absolute;left:0;top:2145px;width:1200px;height:91px;background:var(--footer-bg)}
.footer-nav{display:flex;justify-content:center;gap:40px;padding-top:20px}
.footer-nav a{color:#e3e6e9;font-size:12px;text-decoration:none;text-transform:uppercase;font-weight:600}
.copyright{position:absolute;bottom:0;left:0;width:100%;height:36px;background:var(--footer-bottom);color:#9aa1a8;font-size:12px;text-align:center;line-height:36px}
</style>
</head>
<body>
<header class="site-header">
  <div class="brand"><span class="brand-mark"></span><span class="brand-name">Plexora Buyer<br>Records Hub</span></div>
  <div class="search">Enter search terms</div>
  <div class="social"><span></span><span></span><span></span><span></span></div>
</header>
<nav class="main-nav">
  <a class="active" href="#">Home</a><a href="#">Search by Name</a><a href="#">VIN Lookup</a><a href="#">Complete List</a><a href="#">Contact Us</a><a href="#">Advertise</a>
</nav>

<main class="content">
  <section class="hero"><h1>4P7KD29R813560742 Vehicle Purchase Information</h1></section>

  <h2 class="section-title title-customer">Customer Name: <strong>DARA PELLOW</strong></h2>
  <div class="detail-grid">
    <div class="detail-col"><h3>Customer Details</h3><ul>
      <li><b>Address</b> 4807 Fairview Ave</li><li><b>City</b> Harlow Creek</li><li><b>State</b> KY</li><li><b>Zip</b> 42104</li><li><b>Date</b> 2007</li></ul></div>
    <div class="detail-col"><h3>Car Details</h3><ul>
      <li><b>Make</b> CORVANE</li><li><b>Model</b> STELLIX</li><li><b>VIN</b> 4P7KD29R813560742</li><li><b>Trim</b> Coupe Convertible LT1</li><li><b>Engine</b> 6.0L V8 SFI OHV</li></ul></div>
    <div class="detail-col"><h3>Information</h3><ul>
      <li><b>Style</b> CONVERTIBLE 2-DR</li><li><b>Made in</b> UNITED STATES</li><li><b>Seating</b> 2 (std.)</li><li><b>Curb weight</b> 3199 lbs</li><li><b>Overall length</b> 174.6 in</li></ul></div>
    <div class="detail-col"><h3>Features</h3><ul>
      <li><b>Standard Seating</b> 2</li><li><b>Optional Seating</b> Not listed</li><li><b>Highway Mileage</b> 26 mpg</li><li><b>City Mileage</b> 16 mpg</li><li><b>Transmission</b> 6-Speed Manual</li></ul></div>
  </div>

  <h2 class="section-title title-fuel">National Fuel Office Economy Information</h2>
  <div class="fuel-table">
    <div class="fuel-cell"><h4>Barrels 08: 17.3</h4><p>Annual petroleum consumption in barrels for fuel type</p></div>
    <div class="fuel-cell"><h4>Displacement: 6.0</h4><p>Engine displacement in liters</p></div>
    <div class="fuel-cell"><h4>City 08: 16</h4><p>City MPG for fuel type</p></div>
    <div class="fuel-cell"><h4>Drive: RWD</h4><p>Drive axle type of the vehicle</p></div>
    <div class="fuel-cell"><h4>CO2: 592</h4><p>Tailpipe CO2 in grams per mile for fuel type</p></div>
    <div class="fuel-cell"><h4>Highway 08: 26</h4><p>Highway MPG for fuel type</p></div>
    <div class="fuel-cell"><h4>CO2 Tailpipe: 592</h4><p>Tailpipe CO2 in grams per mile for primary fuel</p></div>
    <div class="fuel-cell"><h4>Year: 2007</h4><p>Model year of the vehicle</p></div>
    <div class="fuel-cell"><h4>Comb 08: 19</h4><p>Combined MPG for fuel type</p></div>
    <div class="fuel-cell"><h4>Cylinders: 8</h4><p>Engine cylinders</p></div>
    <div class="fuel-cell"><h4>Fuel Cost 08: 2150</h4><p>Annual fuel cost for fuel type</p></div>
    <div class="fuel-cell"><h4>Fuel Type: Premium</h4><p>Fuel type of the vehicle</p></div>
    <div class="fuel-cell"><h4>Class: Two Seaters</h4><p>Size class of the vehicle</p></div>
    <div class="fuel-cell"><h4>Trany: Manual 6-spd</h4><p>Transmission type of the vehicle</p></div>
  </div>

  <h2 class="section-title title-court">Court Records Search: <strong>DARA PELLOW</strong></h2>
  <div class="action-bar">Click to run a court records search for DARA PELLOW now</div>
  <p class="body-text">A court records search can help confirm the identity of a vehicle buyer and reveal public filings linked to their name. Results may include civil cases, liens, judgments and other open records from county and state courts across the country.</p>

  <h2 class="section-title title-vin">VIN Lookup: <strong>4P7KD29R813560742</strong></h2>
  <div class="action-bar">Click to run a vehicle lookup for VIN 4P7KD29R813560742 now</div>
  <p class="body-text">A full VIN lookup shows the build details, title history, recorded mileage and past ownership for this vehicle. Each character in the code stands for a part of its make, model, plant and year, giving a clear picture of where and how the car was built.</p>
  <p class="body-text">All records on this page are gathered from public purchase filings and open data sources. We update our listings often, yet some details may change over time, so please confirm key facts before you rely on them for any sale or purchase decision.</p>
</main>

<footer class="site-footer">
  <nav class="footer-nav"><a href="#">Home</a><a href="#">Search by Name</a><a href="#">VIN Lookup</a><a href="#">Complete List</a><a href="#">Contact Us</a><a href="#">Advertise</a></nav>
  <div class="copyright">© Copyright 2015 plexora.site. All Rights Reserved.</div>
</footer>
</body>
</html>
```